Vantiqo custom business card design

Need a authentic, innovative business card design for a new mobile app business. I am uploading a few screen images from our app for you to view. I would like app design theme to match business card design. I can also send logo images.

```html
<!DOCTYPE html>
<html lang="en">
<head>
<meta charset="utf-8">
<title>Vantiqo Business Card</title>
<link href="https://fonts.googleapis.com/css2?family=Montserrat:wght@400;700;800&display=swap" rel="stylesheet">
<style>
  :root {
    --purple: #6a0596;
    --purple-deep: #620090;
    --charcoal: #262626;
    --text-grey: #4a4a4a;
    --card-white: #ffffff;
    --backdrop: #e6e6e6;
  }
  * { margin: 0; padding: 0; box-sizing: border-box; }
  html, body {
    width: 1200px; height: 1200px; overflow: hidden;
    background: var(--backdrop);
    font-family: "Montserrat", sans-serif;
  }
  .card {
    position: absolute; left: 262px; width: 686px; height: 392px;
    box-shadow: 0 14px 28px rgba(0,0,0,0.25);
  }
  .card-front { top: 165px; background: var(--card-white); }
  .card-back {
    top: 653px;
    background: linear-gradient(180deg, var(--purple) 0%, var(--purple-deep) 100%);
  }
  .side-strip { position: absolute; left: 0; top: 0; width: 27px; height: 392px; }
  .side-strip .strip-dark { height: 139px; background: var(--charcoal); }
  .side-strip .strip-purple { height: 253px; background: var(--purple); }
  .holder-name {
    position: absolute; left: 50px; top: 50px;
    font-size: 26px; font-weight: 800; color: var(--purple); letter-spacing: 0.5px;
  }
  .holder-title {
    position: absolute; left: 50px; top: 80px;
    font-size: 17px; font-weight: 700; color: var(--charcoal); letter-spacing: 0.4px;
  }
  .address {
    position: absolute; left: 50px; top: 186px;
    font-size: 16px; line-height: 21px; color: var(--text-grey); letter-spacing: 0.3px;
  }
  .contact-list {
    position: absolute; left: 50px; top: 244px; list-style: none;
    font-size: 16px; color: var(--text-grey); letter-spacing: 0.3px;
  }
  .contact-list li { display: flex; align-items: center; height: 22px; }
  .contact-list svg { width: 16px; height: 16px; margin-right: 10px; fill: var(--purple); }
  .brand {
    position: absolute; display: flex; align-items: center; gap: 10px;
    font-weight: 800; white-space: nowrap;
  }
  .brand .brand-dot { border-radius: 50%; flex: none; }
  .brand-front {
    right: 42px; top: 306px; font-size: 34px; color: var(--charcoal);
  }
  .brand-front .brand-dot { width: 18px; height: 18px; background: var(--purple); }
  .brand-back {
    left: 0; right: 0; top: 168px; justify-content: center;
    font-size: 44px; color: var(--card-white);
  }
  .brand-back .brand-dot { width: 22px; height: 22px; background: var(--card-white); }
  .back-url {
    position: absolute; left: 0; right: 0; top: 336px; text-align: center;
    font-size: 15px; color: var(--card-white); letter-spacing: 10px;
  }
</style>
</head>
<body>
  <section class="card card-front">
    <div class="side-strip">
      <div class="strip-dark"></div>
      <div class="strip-purple"></div>
    </div>
    <h1 class="holder-name">MARA ELLISON</h1>
    <p class="holder-title">CEO/FOUNDER</p>
    <p class="address">2140 Alder Crest Road<br>Northgate, Alaska 34518</p>
    <ul class="contact-list">
      <li><svg viewBox="0 0 16 16"><path d="M3 1l3 3-1.5 2c1 2 2.5 3.5 4.5 4.5L11 9l3 3-2 3C6 14 2 10 1 3z"/></svg>555 214 7730</li>
      <li><svg viewBox="0 0 16 16"><path d="M4 0h8a1 1 0 0 1 1 1v14a1 1 0 0 1-1 1H4a1 1 0 0 1-1-1V1a1 1 0 0 1 1-1zm1 2v10h6V2z"/></svg>555 308 6142</li>
      <li><svg viewBox="0 0 16 16"><path d="M4 1h8v5H4zM1 7h14v7H1zm3 3v2h8v-2z"/></svg>555 471 2295</li>
      <li><svg viewBox="0 0 16 16"><path d="M1 4h14v9H1zm1.5 1.2L8 9l5.5-3.8V5h-11z"/></svg>mara@vantiqo.com</li>
      <li><svg viewBox="0 0 16 16"><path d="M8 1a7 7 0 1 0 0 14A7 7 0 0 0 8 1zm-2 3c1 0 2 1 1.5 2S5 7 4 6.5zm4 3c1 0 2 1 2 2.5S10.5 12 10 11 9 8 10 7z"/></svg>www.vantiqo.com</li>
    </ul>
    <div class="brand brand-front">
      <span class="brand-dot"></span>
      <span class="brand-name">Vantiqo</span>
    </div>
  </section>

  <section class="card card-back">
    <div class="brand brand-back">
      <span class="brand-dot"></span>
      <span class="brand-name">Vantiqo</span>
    </div>
    <p class="back-url">www.vantiqo.com</p>
  </section>
</body>
</html>
```